Kelvaro.ch is looking for business card letterhead and envelope C5 with WOW effect

We need a strong business card for our company Kelvaro.ch, logo is available. You want a black or dark background on which the logo Stark r% 26 # 252; appears. Letterhead and envelope in C5 format should be in a similar design, but does not have to be We need a strong business card for our company Kelvaro.ch, logo is available. A black or dark background is desired, on which the logo Stark comes across. The letterhead and the envelope in C5 format should have a similar design.

Target Market(s)

Private customers as well as entrepreneurs

Contact Information for Business Card

E-mail: info@kelvaro-example.ch
Web.www.Kelvaro-example.ch
Tel: +41 ( 0 ) 79 482 6037
Adresse:
Lindenweg 14
9406 Tarnbach

Hier kann man Icons verwenden für Email,Tel und Adressse

Font styles to use
Other font styles liked:
• Dubai,bold

Colors

Designer to choose colors to be used in the design.

Requirements
Must have
• WOW effect
Nice to have
• R% 26 # 252; back business card with our service listings. - VEHICLE LABELING - SHOP WINDOW LABELING - STICKERS AND MUCH MORE ... in red color

```html
<!DOCTYPE html>
<html lang="en">
<head>
<meta charset="utf-8">
<title>Kelvaro.ch business card</title>
<link href="https://fonts.googleapis.com/css2?family=Montserrat:wght@400;500;700&display=swap" rel="stylesheet">
<style>
  :root {
    --backdrop: #2a2a2a;
    --card: #1c1c1c;
    --card-edge: #262626;
    --white: #ffffff;
    --yellow: #f5c211;
    --red: #e0352b;
    --soft: #e8e8e8;
  }
  * { margin: 0; padding: 0; box-sizing: border-box; }
  html, body {
    width: 1200px; height: 852px; overflow: hidden;
    background: var(--backdrop);
    font-family: "Montserrat", sans-serif;
  }
  .stage {
    width: 1200px; height: 852px;
    display: flex; flex-direction: column; align-items: center; justify-content: center;
    gap: 40px;
  }
  .card {
    position: relative;
    width: 640px; height: 366px;
    border-radius: 16px;
    background: linear-gradient(160deg, var(--card-edge), var(--card) 60%);
    color: var(--white);
  }
  .brand {
    position: absolute;
    display: flex; align-items: center; gap: 14px;
  }
  .brand-dot {
    width: 34px; height: 34px; border-radius: 50%;
    background: var(--yellow);
  }
  .brand-name {
    font-weight: 700; color: var(--white);
    letter-spacing: 1px; text-transform: uppercase;
  }
  /* front */
  .card-front .brand { left: 50%; top: 120px; transform: translateX(-50%); }
  .card-front .brand-name { font-size: 44px; }
  .services {
    position: absolute; left: 0; right: 0; top: 222px;
    text-align: center; color: var(--red);
    font-size: 15px; font-weight: 500; letter-spacing: 0.6px; line-height: 1.55;
    text-transform: uppercase;
  }
  /* back */
  .card-back .brand { left: 56px; top: 205px; }
  .card-back .brand-name { font-size: 30px; }
  .divider {
    position: absolute; left: 350px; top: 78px;
    width: 2px; height: 142px; background: var(--yellow);
  }
  .person { position: absolute; left: 380px; top: 80px; }
  .person-name {
    color: var(--yellow); font-size: 22px; font-weight: 500; letter-spacing: 0.3px;
    text-transform: uppercase;
  }
  .person-role { font-size: 15px; margin: 4px 0 12px 18px; }
  .contacts { list-style: none; margin-left: 18px; }
  .contacts li {
    display: flex; align-items: center; gap: 10px;
    font-size: 14px; line-height: 24px; color: var(--soft);
  }
  .contacts svg { width: 14px; height: 14px; flex: none; }
  .address {
    position: absolute; left: 300px; top: 300px;
    font-size: 15px; color: var(--soft); letter-spacing: 0.3px;
  }
</style>
</head>
<body>
<main class="stage">
  <section class="card card-front">
    <div class="brand">
      <span class="brand-dot"></span>
      <span class="brand-name">Kelvaro.ch</span>
    </div>
    <p class="services">Vehicle labeling | Shop window labeling<br>Stickers and much more</p>
  </section>

  <section class="card card-back">
    <div class="brand">
      <span class="brand-dot"></span>
      <span class="brand-name">Kelvaro.ch</span>
    </div>
    <div class="divider"></div>
    <div class="person">
      <p class="person-name">Lukas Brenner</p>
      <p class="person-role">Director</p>
      <ul class="contacts">
        <li>
          <svg viewBox="0 0 16 16" aria-hidden="true"><path d="M3 1.5l3 .5 1 3.5-1.8 1.3a9 9 0 0 0 4 4L10.5 9l3.5 1 .5 3-2 1.8C6.5 14.5 1.5 9.5 1.2 3.5z" fill="var(--yellow)"/></svg>
          +41 ( 0 ) 79 482 6037
        </li>
        <li>
          <svg viewBox="0 0 16 16" aria-hidden="true"><rect x="1.5" y="3.5" width="13" height="9" fill="none" stroke="var(--yellow)" stroke-width="1.5"/><path d="M1.5 3.5L8 9l6.5-5.5" fill="none" stroke="var(--yellow)" stroke-width="1.5"/></svg>
          info@kelvaro-example.ch
        </li>
        <li>
          <svg viewBox="0 0 16 16" aria-hidden="true"><circle cx="8" cy="8" r="6.5" fill="none" stroke="var(--yellow)" stroke-width="1.4"/><ellipse cx="8" cy="8" rx="2.8" ry="6.5" fill="none" stroke="var(--yellow)" stroke-width="1.2"/><path d="M1.5 8h13M2.5 5h11M2.5 11h11" stroke="var(--yellow)" stroke-width="1"/></svg>
          www.Kelvaro-example.ch
        </li>
      </ul>
    </div>
    <p class="address">Lindenweg 14 9406 Tarnbach</p>
  </section>
</main>
</body>
</html>
```